Home Baker of cakes, muffins, cookies and pastries.

I am looking for business cards for my home baking business called " Yum Bea-A Treat " - I want them to be super cute and girly, yet simple and modern at the same time. Pastel colours is what I envision with the main colour being baby pink.

```html
<!DOCTYPE html>
<html lang="en">
<head>
<meta charset="utf-8">
<title>Yum Bea-A Treat — Business Cards</title>
<link href="https://fonts.googleapis.com/css2?family=Arimo:wght@400;700&display=swap" rel="stylesheet">
<style>
  :root {
    --stage: #2b2b2b;
    --card-white: #ffffff;
    --pink: #e9468f;
    --pink-soft: #f4a3c3;
    --pink-faint: #f9d3e2;
    --pink-deep-tint: #f07fb0;
  }
  * { margin: 0; padding: 0; box-sizing: border-box; }
  html, body { width: 1200px; height: 997px; overflow: hidden; }
  body {
    position: relative;
    background: var(--stage);
    font-family: "Arimo", Arial, sans-serif;
  }
  .brand-mark {
    position: absolute;
    left: 950px; top: 170px;
    width: 220px;
    text-align: center;
    color: var(--pink);
    font-size: 22px;
    font-weight: 700;
  }
  .card {
    position: absolute;
    top: 360px;
    width: 492px; height: 295px;
    border-radius: 18px;
    overflow: hidden;
  }
  .card--front { left: 121px; background: var(--card-white); }
  .card--back  { left: 629px; background: var(--pink); }

  .card__decor {
    position: absolute;
    border-radius: 50%;
  }
  .card--front .card__decor {
    left: 370px; top: 20px; width: 200px; height: 200px;
    background: var(--pink-faint);
    opacity: .6;
  }
  .card--back .card__decor {
    left: -80px; top: 30px; width: 190px; height: 190px;
    background: var(--pink-deep-tint);
    opacity: .6;
  }

  .card__brand {
    position: absolute;
    font-weight: 700;
    white-space: nowrap;
  }
  .card--front .card__brand {
    left: 50px; top: 88px;
    font-size: 34px;
    color: var(--pink);
  }
  .card--back .card__brand {
    left: 150px; top: 148px;
    font-size: 36px;
    color: var(--card-white);
  }

  .owner { position: absolute; left: 15px; top: 194px; font-size: 15px; line-height: 18px; }
  .owner__name { color: var(--pink); }
  .owner__role { color: var(--pink-soft); }

  .contact {
    position: absolute;
    display: flex; align-items: center; gap: 7px;
    font-size: 12px;
    color: var(--pink);
  }
  .contact--phone { left: 15px; top: 242px; }
  .contact--email { left: 15px; top: 262px; }
  .contact--social { right: 26px; top: 262px; flex-direction: row-reverse; }
  .contact__icon { width: 12px; height: 12px; display: block; }
</style>
</head>
<body>
  <div class="brand-mark">Yum Bea-A Treat</div>

  <section class="card card--front">
    <div class="card__decor"></div>
    <div class="card__brand">Yum Bea-A Treat</div>
    <div class="owner">
      <p class="owner__name">Beatrice Lane</p>
      <p class="owner__role">Patisserie Chef</p>
    </div>
    <div class="contact contact--phone">
      <svg class="contact__icon" viewBox="0 0 12 12" aria-hidden="true">
        <circle cx="6" cy="6" r="5.5" fill="var(--pink)"/>
        <rect x="4" y="3" width="4" height="6" rx="1" fill="#fff"/>
      </svg>
      <span>0412583907</span>
    </div>
    <div class="contact contact--email">
      <svg class="contact__icon" viewBox="0 0 12 12" aria-hidden="true">
        <circle cx="6" cy="6" r="5.5" fill="var(--pink)"/>
        <rect x="3" y="4" width="6" height="4" fill="#fff"/>
        <path d="M3 4 L6 6.3 L9 4" stroke="var(--pink)" stroke-width=".8" fill="none"/>
      </svg>
      <span>YumBea-aTreat@mailbox.com</span>
    </div>
    <div class="contact contact--social">
      <svg class="contact__icon" viewBox="0 0 12 12" aria-hidden="true">
        <circle cx="6" cy="6" r="5" fill="none" stroke="var(--pink)" stroke-width="1.2"/>
      </svg>
      <span>yum_bea_a_treat</span>
    </div>
  </section>

  <section class="card card--back">
    <div class="card__decor"></div>
    <div class="card__brand">Yum Bea-A Treat</div>
  </section>
</body>
</html>
```